Podiatry clinic requires a modern revamp and editing of existing website.

I would like a fresh new look and updated information for my current business website. An easy to navigate site with prominent address and phone number for call to action. We are a podiatry clinic that focuses on general and sports podiatry.
I would like 4 pages; including Home page, About Us, Services & Contact.
www.brambleridgepodiatry.net

Target Market(s)

Active working professionals.

Industry/Entity Type

Medical

Coding

Coded - Design and coding required

Number of Pages Required

4 page

Font styles to use
Sans Serif

Colors
6b449b

Requirements
Must have
• A modern look with logo and active images; clean and uncluttered. Visible phone number and address for call to action.
• 4 pages - Home, About Us, Services, Contact.
• Home page - update address & service logos.
• About Us - update of personal information.
• Services - Revamp of existing page.
• Contact page to include Google map, email & phone number.
Nice to have
• Ability to add content easily; eg. a blog or adding video onto Home page.
• Link to Facebook page.

```html
<!DOCTYPE html>
<html lang="en">
<head>
<meta charset="utf-8">
<title>Bramble Ridge Podiatry</title>
<link href="https://fonts.googleapis.com/css2?family=Open+Sans:wght@400;600;700&family=Raleway:wght@300;400&display=swap" rel="stylesheet">
<style>
:root{
  --purple:#6b449b;
  --purple-dark:#553580;
  --ink:#444;
  --muted:#777;
  --line:#e2e2e2;
  --band:#f1f1f1;
  --white:#fff;
  --social:#2f8fd8;
}
*{box-sizing:border-box;margin:0;padding:0}
html,body{width:679px;height:1200px;overflow:hidden}
body{font-family:"Open Sans",Arial,sans-serif;color:var(--ink);background:var(--white);position:relative}
.site-header{height:50px;display:flex;align-items:center;padding:0 14px 0 48px;position:relative}
.brand{position:absolute;left:48px;top:0;width:70px;height:62px;background:var(--purple);display:flex;align-items:center;justify-content:center;text-align:center;color:var(--white);font-weight:700;font-size:10px;line-height:1.2;z-index:2}
.main-nav{margin-left:250px;display:flex;gap:14px;font-size:7px;font-weight:700;letter-spacing:.4px}
.main-nav a{color:var(--ink);text-decoration:none}
.header-contact{margin-left:auto;font-size:7px;line-height:1.4;color:var(--ink)}
.social{display:flex;gap:4px;margin-left:10px}
.social span{width:15px;height:15px;background:var(--social);display:block}
.hero{height:335px;position:relative;background:linear-gradient(120deg,#3c3c3c,#8a8a8a 45%,#2c2c2c);color:var(--white);text-align:center}
.hero-title{font-family:"Raleway",Arial,sans-serif;font-weight:300;font-size:38px;padding-top:60px;line-height:1.15;letter-spacing:1px}
.hero-sub{font-size:13px;margin-top:12px;line-height:1.35}
.hero-btn{display:inline-block;margin-top:14px;border:1px solid var(--white);font-size:7px;padding:5px 10px;font-weight:600}
.dots{position:absolute;bottom:14px;left:0;right:0;display:flex;justify-content:center;gap:5px}
.dots i{width:5px;height:5px;border-radius:50%;background:rgba(255,255,255,.6)}
.dots i:first-child{background:var(--white)}
.intro-label{text-align:center;font-size:8px;color:var(--purple);padding:10px 0 6px;border-bottom:1px solid var(--line);margin:0 70px;font-weight:600}
.intro{display:flex;gap:24px;padding:14px 70px 0}
.intro-photo{width:150px;height:190px;background:linear-gradient(160deg,#c9a883,#7a5a3f 60%,#4a3a2d);flex:none}
.intro-text h2{font-size:16px;color:var(--social);font-weight:600;line-height:1.3}
.intro-text .lead{font-size:15px;color:var(--purple);font-weight:600;line-height:1.3;margin-top:10px}
.intro-text .small{font-size:8px;color:var(--muted);line-height:1.5;margin-top:10px}
.products-title{text-align:center;font-size:12px;font-weight:700;margin-top:82px;color:var(--ink)}
.products-title::after{content:"";display:block;width:200px;height:1px;background:var(--line);margin:8px auto 0}
.products{display:flex;gap:22px;padding:22px 30px 0}
.product{flex:1;text-align:center}
.product-photo{height:135px}
.product h3{font-size:10px;font-weight:700;margin-top:12px}
.product p{font-size:7px;color:var(--muted);line-height:1.55;margin-top:7px;padding:0 4px}
.partners{position:absolute;top:1017px;left:0;right:0;height:58px;background:var(--band);display:flex;align-items:center;justify-content:space-around;padding:0 40px}
.partners span{width:100px;height:26px;background:#bcbcbc;display:block}
.site-footer{position:absolute;top:1085px;left:0;right:0;bottom:0;background:var(--purple);color:var(--white)}
.footer-cols{display:flex;padding:14px 28px 0;gap:20px}
.footer-col{flex:1;font-size:6.5px;line-height:1.6}
.footer-col h4{font-size:9px;font-weight:700;margin-bottom:5px}
.footer-bar{position:absolute;bottom:0;left:0;right:0;height:20px;background:var(--purple-dark);display:flex;align-items:center;justify-content:space-between;padding:0 28px;font-size:6.5px}
</style>
</head>
<body>
<header class="site-header">
  <div class="brand">Bramble<br>Ridge<br>Podiatry</div>
  <nav class="main-nav"><a href="#">HOME</a><a href="#">ABOUT US</a><a href="#">SERVICES</a><a href="#">BLOG</a></nav>
  <div class="header-contact">Suite 12 / 240 Harlow Street Melbourne 3000<br>1300 555 018</div>
  <div class="social"><span></span><span></span><span></span></div>
</header>

<section class="hero" role="img" aria-label="Runner's feet on a track">
  <h1 class="hero-title">Welcome to<br>Bramble Ridge Podiatry</h1>
  <p class="hero-sub">We are a podiatry clinic that focuses<br>on general and sports podiatry</p>
  <span class="hero-btn">ABOUT US</span>
  <div class="dots"><i></i><i></i><i></i><i></i></div>
</section>

<p class="intro-label">Welcome to Bramble Ridge Podiatry</p>
<section class="intro">
  <div class="intro-photo" role="img" aria-label="Athlete tying his running shoe"></div>
  <div class="intro-text">
    <h2>Bramble Ridge Podiatry is a Podiatry clinic in the heart of Melbourne CBD. We are located between Fenwick &amp; Ashby Streets in the Southgate Business Centre.</h2>
    <p class="lead">Our podiatrists are fully qualified health professionals who are able to diagnose, treat, manage or help to prevent all medical conditions that affect the feet and lower limbs.</p>
    <p class="small">We provide General Podiatry Treatment and some Specialised Services in relation to various foot conditions, including Sports Injuries, Orthotic Therapy and Nail Surgery.</p>
  </div>
</section>

<h2 class="products-title">Podiatry &amp; Footwear Wellness Products</h2>
<section class="products">
  <article class="product">
    <div class="product-photo" role="img" aria-label="Hands treating a foot" style="background:linear-gradient(135deg,#f0dccb,#d9b99e)"></div>
    <h3>Podiatry Treatments</h3>
    <p>Podiatrists are trained to diagnose and treat all medical conditions that affect the feet and lower limbs. At Bramble Ridge Podiatry we provide treatment for general and sports podiatry conditions and various specialised services.</p>
  </article>
  <article class="product">
    <div class="product-photo" role="img" aria-label="Orthotic insole on white" style="background:linear-gradient(135deg,#f5ede2,#d8c0a0)"></div>
    <h3>Podiatry Products Footwear</h3>
    <p>At Bramble Ridge Podiatry we stock and recommend various products and footwear that aid in maintaining optimal foot health and comfort every day.</p>
  </article>
  <article class="product">
    <div class="product-photo" role="img" aria-label="Family walking outdoors on a sunny day" style="background:linear-gradient(160deg,#a9cfe8,#e9d9b8 70%,#8fb56f)"></div>
    <h3>Health Wellness Products</h3>
    <p>At Bramble Ridge Podiatry we believe that maintaining a healthy &amp; active lifestyle is the best way to prevent or manage debilitating foot conditions. We like to promote a healthy diet &amp; exercise between treatment visits.</p>
  </article>
</section>

<section class="partners" aria-label="Partners"><span></span><span></span><span></span><span></span></section>

<footer class="site-footer">
  <div class="footer-cols">
    <div class="footer-col"><h4>Contact</h4>Please feel free to contact us for any query. You reach us by phone, email or simply visit our clinic during opening hours.</div>
    <div class="footer-col"><h4>Phone number</h4>Phone 1 : 1300 555 018<br>Phone 2 : 1300 555 019</div>
    <div class="footer-col"><h4>Office</h4>Address: Suite 12 / 240 Harlow Street<br>City: Melbourne 3000</div>
    <div class="footer-col"><h4>E-Mail</h4>info@brambleridgepodiatry.net</div>
  </div>
  <div class="footer-bar"><span>Copyright © 2015 Bramble Ridge Podiatry</span><span>Website: www.brambleridgepodiatry.net</span></div>
</footer>
</body>
</html>
```